VENTURE CAPITAL GROUP BUSINESS CARD DESIGN

Venture Capital Group based in SF looking for a bold business card design. No trendy colour explosion, 3D effects etc. Just "simple" optical effects. Works on your brain, keeps your eye focused and sticks to your mind.
Target Market(s)
Technology startups
Industry/Entity Type
Venture Capital
Contact Information for Business Card
DESMOND WHITLAKE
MANAGING PARTNER
187 FENWORTH ST SAN FRANCISCO, CA 94187
415.555.0142 O
415.555.0147 F
415.555.0193 C
desmond@veldtmoorcapital.ventures

```html
<!DOCTYPE html>
<html lang="en">
<head>
<meta charset="UTF-8">
<title>Veldtmoor Capital Group – Business Card</title>
<link href="https://fonts.googleapis.com/css2?family=Cinzel:wght@400;600&family=Arimo:wght@400&display=swap" rel="stylesheet">
<style>
  :root {
    --page-bg: #e9e8e4;
    --card-bg: #ffffff;
    --card-shade: #f1f1f1;
    --brand-green: #1f7a2e;
    --text-grey: #5a5a5a;
    --icon-green: #2f8a3c;
  }
  * { box-sizing: border-box; margin: 0; padding: 0; }
  html, body {
    width: 1200px; height: 950px; overflow: hidden;
    background: var(--page-bg);
  }
  .sheet { position: relative; width: 1200px; height: 950px; }
  .card {
    position: absolute; left: 250px; width: 700px; height: 400px;
    background: linear-gradient(160deg, var(--card-bg) 55%, var(--card-shade));
    box-shadow: 0 6px 18px rgba(0,0,0,0.18);
    overflow: hidden;
  }
  .card--back { top: 50px; }
  .card--front { top: 500px; }

  .brand {
    position: absolute; color: var(--brand-green);
    font-family: "Cinzel", serif; font-weight: 400;
    text-align: center; line-height: 1;
  }
  .brand__name { display: block; letter-spacing: 1px; }
  .brand__tag { display: block; letter-spacing: 6px; margin-top: 6px; }
  .card--back .brand { left: 0; right: 0; top: 160px; }
  .card--back .brand__name { font-size: 50px; }
  .card--back .brand__tag { font-size: 13px; }
  .card--front .brand { right: 40px; top: 318px; width: 360px; }
  .card--front .brand__name { font-size: 46px; }
  .card--front .brand__tag { font-size: 12px; }

  .contact {
    position: absolute; right: 40px; top: 52px; width: 380px;
    text-align: right; color: var(--text-grey);
  }
  .contact__name {
    font-family: "Cinzel", serif; font-weight: 600;
    font-size: 24px; color: var(--brand-green); letter-spacing: 1px;
  }
  .contact__title {
    font-family: "Cinzel", serif; font-weight: 400;
    font-size: 17px; letter-spacing: 1.5px; margin-top: 2px;
  }
  .contact__address {
    font-family: "Arimo", sans-serif; font-size: 17px;
    line-height: 24px; margin-top: 16px; font-style: normal;
  }
  .contact__lines { list-style: none; margin-top: 8px; }
  .contact__line {
    font-family: "Arimo", sans-serif; font-size: 17px; line-height: 25px;
    display: flex; justify-content: flex-end; align-items: center; gap: 8px;
  }
  .contact__line svg { width: 16px; height: 16px; fill: var(--icon-green); flex: none; }
</style>
</head>
<body>
<main class="sheet">
  <section class="card card--back" aria-label="Card back">
    <div class="brand">
      <span class="brand__name">VELDTMOOR</span>
      <span class="brand__tag">CAPITAL GROUP</span>
    </div>
  </section>

  <section class="card card--front" aria-label="Card front">
    <div class="contact">
      <h1 class="contact__name">Desmond Whitlake</h1>
      <p class="contact__title">Managing Partner</p>
      <address class="contact__address">187 Fenworth ST San Francisco<br>CA 94187</address>
      <ul class="contact__lines">
        <li class="contact__line">415.555.0142
          <svg viewBox="0 0 16 16" aria-label="Office"><path d="M1 5c2-3 12-3 14 0v2h-4V5.5H5V7H1z"/><rect x="3" y="8" width="10" height="7" rx="1"/></svg>
        </li>
        <li class="contact__line">415.555.0193
          <svg viewBox="0 0 16 16" aria-label="Mobile"><path d="M4 0h8a1 1 0 0 1 1 1v14a1 1 0 0 1-1 1H4a1 1 0 0 1-1-1V1a1 1 0 0 1 1-1zm1 2v10h6V2z"/></svg>
        </li>
        <li class="contact__line">415.555.0147
          <svg viewBox="0 0 16 16" aria-label="Fax"><rect x="4" y="1" width="8" height="5"/><rect x="1" y="6" width="14" height="9" rx="1"/></svg>
        </li>
        <li class="contact__line">desmond@veldtmoorcapital.ventures
          <svg viewBox="0 0 16 16" aria-label="Email"><path d="M1 3h14v10H1zm1 1.5V5l6 4 6-4v-.5z"/></svg>
        </li>
      </ul>
    </div>
    <div class="brand">
      <span class="brand__name">VELDTMOOR</span>
      <span class="brand__tag">CAPITAL GROUP</span>
    </div>
  </section>
</main>
</body>
</html>
```